Web Design Project - Shipping Industry

Goals and Objectives
The objective of the new website is to create a more modern look and feel. The site will also allow for a more effective means of communicating with members while providing the public with information and developments in the local, regional and international shipping industry.
Scope
The website will highlight the history of the organisation inclusive of text and photographs. It will take visitors through the years from beginning to present. Information on the history of the shipping industry will also be included.
It will feature current articles on the organisation, its members and stakeholders in the shipping industry. Member information as well as pertinent details regarding the organisation’s subsidiaries will be documented for the website.
Information as it relates to shipping statistics, case studies, laws and regulations, international treaties and trade documents, shipping terms, careers in shipping, job opportunities, training opportunities, information for shippers including port listing and trade lanes will be main features of the content for the website.
The Association’s community involvement, industry calendar events and related links relevant industry members will also be featured.
Target Market
• The General Public;
• Members of the organization;
• Shipping Industry Stakeholders (local, regional and international);
• Tertiary students conducting research.
• Potential employees
• Potential Business Partners
Best Practice Bench Marketing
The following websites are being looked at:
• Korvel Quayworks - http://www.korvelquayworks.example/ (preferred look)
• Tessaly Maritime Association - http://www.tma-freight.example/ (like image transition on main page)
• Drovna - http://www.drovna.example (professional look)
• PLW - http://www.pelworth.example (preferred color: blue in logo)
• Quillo - http://www.quillo.example/electronics/tv-video-audio/ (preferred look for links page: image + short text below + visit site link)
Expected Result
• 3 - 5 pages which must include: [1] main page [2] standard page [3] links page

```html
<!DOCTYPE html>
<html lang="en">
<head>
<meta charset="utf-8">
<title>Kestravo – Links</title>
<link rel="stylesheet" href="https://fonts.googleapis.com/css2?family=Source+Sans+3:wght@400;600;700&family=Michroma&display=swap">
<style>
  :root {
    --canvas: #e9e9e9;
    --page: #ffffff;
    --navy: #2b2862;
    --ink: #111111;
    --blue-top: #3b78dc;
    --blue-bottom: #1a4cbf;
    --gold: #f0c419;
    --green: #5aa51b;
    --line: #d6d6d6;
  }
  * { box-sizing: border-box; margin: 0; padding: 0; }
  html, body { width: 1200px; height: 971px; overflow: hidden; background: var(--canvas); }
  body { font-family: "Source Sans 3", sans-serif; color: var(--ink); }
  .page { position: absolute; left: 100px; top: 0; width: 997px; height: 971px; background: var(--page); }
  .account { position: absolute; right: 41px; top: 12px; font-size: 14px; }
  .account span { margin: 0 6px; }
  .brand { position: absolute; left: 41px; top: 61px; font-family: "Michroma", sans-serif; font-size: 25px; letter-spacing: 3px; color: var(--navy); line-height: 1; }
  .social { position: absolute; left: 657px; top: 66px; display: flex; gap: 6px; }
  .social i { width: 14px; height: 14px; background: #6b8fc4; border-radius: 2px; display: block; }
  .search { position: absolute; left: 741px; top: 60px; width: 221px; height: 25px; border: 1px solid var(--line); font-size: 13px; padding: 4px 10px; color: #222; }
  .search svg { position: absolute; right: 8px; top: 5px; }
  .main-nav { position: absolute; left: 39px; top: 126px; width: 923px; height: 48px; border-top: 3px solid var(--gold); background: linear-gradient(var(--blue-top), var(--blue-bottom)); display: flex; }
  .main-nav a { color: #fff; text-decoration: none; font-size: 11.5px; font-weight: 700; display: flex; align-items: center; justify-content: center; border-right: 1px solid rgba(255,255,255,.18); }
  .main-nav a:last-child { border-right: 0; }
  .hero { position: absolute; left: 39px; top: 174px; width: 923px; height: 227px; background: linear-gradient(100deg, #1e5d88 0%, #4b7b68 25%, #9aa5a0 45%, #e8ecee 60%, #5d9fc5 78%, #1f5c92 100%); }
  .section-title { position: absolute; left: 39px; top: 424px; font-family: "Michroma", sans-serif; font-size: 26px; color: var(--navy); font-weight: 400; }
  .links { position: absolute; left: 40px; top: 470px; display: grid; grid-template-columns: repeat(4, 203px); column-gap: 36px; }
  .link-card { height: 218px; }
  .link-card .thumb { width: 203px; height: 101px; }
  .link-card h3 { font-family: "Michroma", sans-serif; font-size: 10px; font-weight: 400; margin-top: 9px; white-space: nowrap; }
  .link-card p { font-size: 11.5px; line-height: 15px; margin-top: 6px; width: 205px; }
  .visit { display: inline-flex; align-items: center; gap: 6px; margin-top: 5px; color: var(--green); font-size: 12px; font-weight: 700; text-decoration: none; }
  .footer { position: absolute; left: 0; bottom: 0; width: 997px; height: 45px; background: linear-gradient(var(--blue-bottom), var(--blue-top)); color: #fff; font-size: 11px; display: flex; align-items: center; justify-content: space-between; padding: 0 56px 0 40px; }
  .footer nav a { color: #fff; text-decoration: none; }
  .footer nav span { margin: 0 12px; }
  .t1 { background: linear-gradient(90deg, #c7c3bf, #b23a35 60%, #6f6a66); }
  .t2 { background: linear-gradient(120deg, #4e86c5, #c9d7e3 50%, #3a74b8); }
  .t3 { background: linear-gradient(180deg, #9cc0de, #e0e4e6 55%, #34495e); }
  .t4 { background: linear-gradient(150deg, #b6283a, #7b8894 60%, #c8ccd0); }
  .t5 { background: linear-gradient(135deg, #0d3f77, #5fa4d2 50%, #0a2a55); }
  .t6 { background: linear-gradient(180deg, #5c7f9a, #b26a3e 55%, #2c4a66); }
  .t7 { background: linear-gradient(180deg, #8eb2cc, #a54b36 55%, #2c5a7f); }
  .t8 { background: linear-gradient(160deg, #8d8f90, #b27d6c 50%, #7b8a96); }
</style>
</head>
<body>
<div class="page">
  <div class="account"><a>Register</a><span>|</span><a>Login</a></div>
  <div class="brand">KESTRAVO</div>
  <div class="social" aria-label="Social links"><i></i><i></i><i></i><i></i></div>
  <div class="search">Search
    <svg width="14" height="14" viewBox="0 0 14 14"><circle cx="8.5" cy="5.5" r="4" fill="none" stroke="#bbb" stroke-width="1.3"/><line x1="5.6" y1="8.4" x2="1.5" y2="12.5" stroke="#bbb" stroke-width="1.6"/></svg>
  </div>
  <nav class="main-nav">
    <a style="width:90px">HOME</a><a style="width:105px">ABOUT US</a><a style="width:114px">PRODUCTS</a><a style="width:102px">SERVICES</a><a style="width:82px">NEWS</a><a style="width:101px">SUPPORT</a><a style="width:110px">PARTNERS</a><a style="width:118px">CUSTOMERS</a><a style="width:101px">CONTACT</a>
  </nav>
  <div class="hero" role="img" aria-label="Aerial photo of a container ship cutting through blue sea"></div>

  <h1 class="section-title">LINKS</h1>
  <div class="links">
    <article class="link-card"><div class="thumb t1" role="img" aria-label="Ship docked beside red port cranes"></div><h3>PELWORTH.EXAMPLE</h3><p>Lorem ipsum dolor sit amet, consectetur adipisicing elit, sed do eiusmod tempor</p><a class="visit">VISIT WEBSITE <svg width="15" height="15" viewBox="0 0 15 15"><circle cx="7.5" cy="7.5" r="7" fill="var(--green)"/><path d="M4 7.5h6M7.5 4.5l3 3-3 3" stroke="#fff" stroke-width="1.6" fill="none"/></svg></a></article>
    <article class="link-card"><div class="thumb t2" role="img" aria-label="Ship bow and crane against city skyline"></div><h3>HARBORLINE.EXAMPLE</h3><p>Lorem ipsum dolor sit amet, consectetur adipisicing elit, sed do eiusmod tempor</p><a class="visit">VISIT WEBSITE <svg width="15" height="15" viewBox="0 0 15 15"><circle cx="7.5" cy="7.5" r="7" fill="var(--green)"/><path d="M4 7.5h6M7.5 4.5l3 3-3 3" stroke="#fff" stroke-width="1.6" fill="none"/></svg></a></article>
    <article class="link-card"><div class="thumb t3" role="img" aria-label="White cargo ship superstructure with containers"></div><h3>CARGOWRIGHT.EXAMPLE</h3><p>Lorem ipsum dolor sit amet, consectetur adipisicing elit, sed do eiusmod tempor</p><a class="visit">VISIT WEBSITE <svg width="15" height="15" viewBox="0 0 15 15"><circle cx="7.5" cy="7.5" r="7" fill="var(--green)"/><path d="M4 7.5h6M7.5 4.5l3 3-3 3" stroke="#fff" stroke-width="1.6" fill="none"/></svg></a></article>
    <article class="link-card"><div class="thumb t4" role="img" aria-label="Red ship hull moored at a quay"></div><h3>CARGOWRIGHT.EXAMPLE</h3><p>Lorem ipsum dolor sit amet, consectetur adipisicing elit, sed do eiusmod tempor</p><a class="visit">VISIT WEBSITE <svg width="15" height="15" viewBox="0 0 15 15"><circle cx="7.5" cy="7.5" r="7" fill="var(--green)"/><path d="M4 7.5h6M7.5 4.5l3 3-3 3" stroke="#fff" stroke-width="1.6" fill="none"/></svg></a></article>
    <article class="link-card"><div class="thumb t5" role="img" aria-label="Blue world map with a compass"></div><h3>DUNEGATE.EXAMPLE</h3><p>Lorem ipsum dolor sit amet, consectetur adipisicing elit, sed do eiusmod tempor</p><a class="visit">VISIT WEBSITE <svg width="15" height="15" viewBox="0 0 15 15"><circle cx="7.5" cy="7.5" r="7" fill="var(--green)"/><path d="M4 7.5h6M7.5 4.5l3 3-3 3" stroke="#fff" stroke-width="1.6" fill="none"/></svg></a></article>
    <article class="link-card"><div class="thumb t6" role="img" aria-label="Loaded container ship at sea"></div><h3>TIDEWAYAGENTS.EXAMPLE</h3><p>Lorem ipsum dolor sit amet, consectetur adipisicing elit, sed do eiusmod tempor</p><a class="visit">VISIT WEBSITE <svg width="15" height="15" viewBox="0 0 15 15"><circle cx="7.5" cy="7.5" r="7" fill="var(--green)"/><path d="M4 7.5h6M7.5 4.5l3 3-3 3" stroke="#fff" stroke-width="1.6" fill="none"/></svg></a></article>
    <article class="link-card"><div class="thumb t7" role="img" aria-label="Container ship sailing on open water"></div><h3>GLOBALHULL.EXAMPLE</h3><p>Lorem ipsum dolor sit amet, consectetur adipisicing elit, sed do eiusmod tempor</p><a class="visit">VISIT WEBSITE <svg width="15" height="15" viewBox="0 0 15 15"><circle cx="7.5" cy="7.5" r="7" fill="var(--green)"/><path d="M4 7.5h6M7.5 4.5l3 3-3 3" stroke="#fff" stroke-width="1.6" fill="none"/></svg></a></article>
    <article class="link-card"><div class="thumb t8" role="img" aria-label="Aerial view of a container terminal yard"></div><h3>QUAYFED.EXAMPLE</h3><p>Lorem ipsum dolor sit amet, consectetur adipisicing elit, sed do eiusmod tempor</p><a class="visit">VISIT WEBSITE <svg width="15" height="15" viewBox="0 0 15 15"><circle cx="7.5" cy="7.5" r="7" fill="var(--green)"/><path d="M4 7.5h6M7.5 4.5l3 3-3 3" stroke="#fff" stroke-width="1.6" fill="none"/></svg></a></article>
  </div>

  <footer class="footer">
    <div>© DOCKSIDE SYSTEMS | ALL RIGHT RESERVED</div>
    <nav><a>LEGAL NOTICE</a><span>|</span><a>PRIVACY POLICY</a><span>|</span><a>CONTACT US</a></nav>
  </footer>
</div>
</body>
</html>
```